graphic showing our process of education as a process called a pipeline

Also see my updated comments on discussion section.
Title of the graphic needs to be:
TITLE = The KESIMA Strategic Leadership Pipeline = larger, bold heading
SUB-TITLE = Developing a steady flow of servant leaders for Tanzania's future = under title; smaller font
change the text for each of the 7 steps to match the outcomes listed on the newly attached PDF (strategic pipeline 11x17)
Pipe should be straight or mostly straight.
Pipe should not be in a strong or dark color.
Any icons or symbols should be simple and professional, not like cartoon or childish.
We need a graphic design that shows our PROCESS, called a "pipeline," that is creating future leaders. We are a US-based non-profit that operates a Christian school in rural Tanzania for 600 students (pre-K through 12th grade). It starts with child sponsorship program that allows poor children and orphans to attend school, we have a primary school (like USA elementary school, pre-K thru 7th), and are building a secondary boarding school (like USA middle and high school, grades 8-12), where students will live on campus in dormitories. We offer education, scholarships, leadership development experiences, help finding and securing college scholarships, academic and career counseling, placements for internships and jobs, and networking and leadership development content and events to create the next generation of servant leaders for the country. Prominent colors should probably be the green, blue and black in the Tanzania flag; we want the design to communicate "smart" and "strategic." The stages of the pipeline need to be properly named; we need to show a "leak" in the pipeline after the primary school because we currently have to send our students AWAY to other boarding schools because we don't have one. As the attached recording says, this is bad for their progress. The attached pipeline graphic is very rough and NOT meant to be imitated. It is factually correct, but is busy and not attractive.

Target Market(s)

Major financial contributors and foundations that want to give money to the cause

Industry/Entity Type

non-profit/Christian ministry in education

Font styles to use
Sans Serif

Requirements
Must have
• A "smart" and strategic" feel; preferably visible when on a half page
Nice to have
• a smart, sophisticated, serious look and feel
Should not have
• an elementary school feel

```html
<!DOCTYPE html>
<html lang="en">
<head>
<meta charset="UTF-8">
<title>KESIMA Leadership Pipeline</title>
<link rel="stylesheet" href="https://fonts.googleapis.com/css2?family=Montserrat:wght@400;500;600;700;800&display=swap">
<style>
  :root {
    --ink: #111418;
    --brand-blue: #1a9fdc;
    --flange-blue: #1797d6;
    --pipe-blue: #b6e2f6;
    --pipe-green: #a6ecc9;
    --accent-green: #2dbb3a;
    --card-border: #8fd0ef;
    --paper: #ffffff;
  }
  * { box-sizing: border-box; margin: 0; padding: 0; }
  html, body { width: 1200px; height: 1200px; overflow: hidden; background: var(--paper); }
  body { font-family: "Montserrat", Arial, sans-serif; color: var(--ink); position: relative; }

  .pipeline-panel { position: absolute; left: 0; width: 1200px; height: 557px; }
  .pipeline-panel--with-leak { top: 0; }
  .pipeline-panel--sealed { top: 557px; }

  .pipeline-art { position: absolute; left: 0; top: 0; width: 1200px; height: 557px; }

  .panel-title {
    position: absolute; left: 0; right: 0; top: 104px;
    text-align: center; font-weight: 800; font-size: 39px;
    color: var(--brand-blue); letter-spacing: 0.2px; line-height: 1;
  }
  .panel-subtitle {
    position: absolute; left: 0; right: 0; top: 154px;
    text-align: center; font-weight: 600; font-size: 15.5px; line-height: 1;
  }

  .stage-card {
    position: absolute; top: 220px; width: 96px; height: 147px;
    background: var(--paper);
    border: 1.5px dotted var(--card-border);
    border-radius: 8px;
    text-align: center;
  }
  .stage-name {
    background: var(--brand-blue); color: #fff;
    border-radius: 7px 7px 0 0;
    height: 48px; margin: -1.5px -1.5px 0;
    display: flex; align-items: center; justify-content: center;
    font-size: 7.6px; font-weight: 700; line-height: 1.25;
    text-transform: uppercase; padding: 4px 5px;
  }
  .stage-tag {
    display: inline-block; margin-top: 3px;
    background: var(--accent-green); color: #fff;
    font-size: 7px; font-weight: 700; letter-spacing: 0.3px;
    padding: 2px 7px; border-radius: 2px;
  }
  .stage-outcome {
    font-size: 8.1px; font-weight: 500; line-height: 1.3;
    padding: 5px 7px 0;
  }
</style>
</head>
<body>

<!-- Panel with leak after primary school -->
<section class="pipeline-panel pipeline-panel--with-leak">
  <svg class="pipeline-art" viewBox="0 0 1200 557" xmlns="http://www.w3.org/2000/svg">
    <line x1="266" y1="163" x2="328" y2="163" stroke="#2dbb3a" stroke-width="2"/>
    <line x1="915" y1="163" x2="977" y2="163" stroke="#2dbb3a" stroke-width="2"/>
    <rect x="250" y="245" width="750" height="13" fill="#b6e2f6"/>
    <g fill="#2dbb3a">
      <rect x="298" y="243" width="4" height="17"/><rect x="327" y="243" width="4" height="17"/>
      <rect x="422" y="243" width="4" height="17"/><rect x="451" y="243" width="4" height="17"/>
      <rect x="546" y="243" width="4" height="17"/><rect x="575" y="243" width="4" height="17"/>
      <rect x="670" y="243" width="4" height="17"/><rect x="699" y="243" width="4" height="17"/>
      <rect x="794" y="243" width="4" height="17"/><rect x="823" y="243" width="4" height="17"/>
      <rect x="918" y="243" width="4" height="17"/><rect x="947" y="243" width="4" height="17"/>
    </g>
    <rect x="188" y="411" width="860" height="24" fill="#b6e2f6"/>
    <g fill="#1797d6">
      <rect x="186" y="406" width="5" height="34"/><rect x="193" y="406" width="3" height="34"/>
      <rect x="1043" y="406" width="3" height="34"/><rect x="1048" y="406" width="5" height="34"/>
      <rect x="306" y="408" width="4" height="30"/><rect x="312" y="408" width="4" height="30"/>
      <rect x="430" y="408" width="4" height="30"/><rect x="436" y="408" width="4" height="30"/>
      <rect x="554" y="408" width="4" height="30"/><rect x="560" y="408" width="4" height="30"/>
      <rect x="678" y="408" width="4" height="30"/><rect x="684" y="408" width="4" height="30"/>
      <rect x="802" y="408" width="4" height="30"/><rect x="808" y="408" width="4" height="30"/>
      <rect x="926" y="408" width="4" height="30"/><rect x="932" y="408" width="4" height="30"/>
    </g>
    <g fill="none" stroke="#a6ecc9" stroke-width="22">
      <path d="M253 367 V398 Q253 423 282 423"/>
      <path d="M377 367 V398 Q377 423 406 423"/>
      <path d="M501 367 V398 Q501 423 530 423"/>
      <path d="M625 367 V398 Q625 423 654 423"/>
      <path d="M749 367 V398 Q749 423 778 423"/>
      <path d="M873 367 V398 Q873 423 902 423"/>
      <path d="M997 367 V398 Q997 423 1026 423"/>
    </g>
    <g fill="#2dbb3a">
      <rect x="241" y="365" width="24" height="4"/><rect x="365" y="365" width="24" height="4"/>
      <rect x="489" y="365" width="24" height="4"/><rect x="613" y="365" width="24" height="4"/>
      <rect x="737" y="365" width="24" height="4"/><rect x="861" y="365" width="24" height="4"/>
      <rect x="985" y="365" width="24" height="4"/>
    </g>
    <g stroke="#1a9fdc" stroke-width="2" stroke-dasharray="2 3">
      <line x1="376" y1="437" x2="376" y2="490"/><line x1="500" y1="437" x2="500" y2="490"/>
      <line x1="624" y1="437" x2="624" y2="490"/><line x1="748" y1="437" x2="748" y2="490"/>
      <line x1="872" y1="437" x2="872" y2="490"/><line x1="996" y1="437" x2="996" y2="490"/>
      <line x1="253" y1="437" x2="253" y2="490"/>
    </g>
    <g class="leak">
      <polyline points="446,415 440,425 448,427 441,440" fill="none" stroke="#1a9fdc" stroke-width="2.5" stroke-linejoin="round"/>
      <path d="M441 449 Q434 460 436 465 A6 6 0 0 0 447 465 Q448 460 441 449 Z" fill="#1a9fdc"/>
      <path d="M452 458 Q446 467 448 471 A5 5 0 0 0 457 471 Q458 467 452 458 Z" fill="#1a9fdc"/>
    </g>
    <g fill="#111418">
      <rect x="233" y="493" width="40" height="48" rx="4" role="img" aria-label="Icon: sponsor with child"/>
      <rect x="362" y="493" width="28" height="48" rx="4" role="img" aria-label="Icon: young child"/>
      <rect x="480" y="493" width="40" height="48" rx="4" role="img" aria-label="Icon: student with science symbol"/>
      <rect x="604" y="493" width="40" height="48" rx="4" role="img" aria-label="Icon: person helping another up"/>
      <rect x="722" y="497" width="52" height="40" rx="4" role="img" aria-label="Icon: graduation cap"/>
      <rect x="850" y="493" width="44" height="48" rx="4" role="img" aria-label="Icon: two people shaking hands"/>
      <rect x="970" y="491" width="54" height="52" rx="4" role="img" aria-label="Icon: crowd of people"/>
    </g>
  </svg>

  <h1 class="panel-title">KESIMA Leadership Pipeline</h1>
  <p class="panel-subtitle">Developing a steady flow of servant leaders for Tanzania's future</p>

  <div class="stage-card" style="left:205px"><div class="stage-name">KESIMA Sponsorship Program</div><span class="stage-tag">OUTCOME</span><p class="stage-outcome">Establishing spiritual, academic,and health foundations</p></div>
  <div class="stage-card" style="left:329px"><div class="stage-name">KESIMA Primary School</div><span class="stage-tag">OUTCOME</span><p class="stage-outcome">Potential leaders with Biblical worldview and strong academic foundations.</p></div>
  <div class="stage-card" style="left:453px"><div class="stage-name">KESIMA Secondary School</div><span class="stage-tag">OUTCOME</span><p class="stage-outcome">Emerging leaders with concrete skills and strong servant mindset.</p></div>
  <div class="stage-card" style="left:577px"><div class="stage-name">KESIMA Service Leadership Experience</div><span class="stage-tag">OUTCOME</span><p class="stage-outcome">Growing servant leaders with practical experience to effect change for the kingdom</p></div>
  <div class="stage-card" style="left:701px"><div class="stage-name">KESIMA Higher Education Support</div><span class="stage-tag">OUTCOME</span><p class="stage-outcome">Expanding vision, capability, and motivation to solve bigger challenges for the nation.</p></div>
  <div class="stage-card" style="left:825px"><div class="stage-name">KESIMA Employment Center</div><span class="stage-tag">OUTCOME</span><p class="stage-outcome">Capable Christ-centered leaders in the marketplace as value adding employees and entrepreneurs.</p></div>
  <div class="stage-card" style="left:949px"><div class="stage-name">KESIMA Leadership Hub</div><span class="stage-tag">OUTCOME</span><p class="stage-outcome">Mature Christian leaders being placed and positioned for leadership roles in the community and nation.</p></div>
</section>

<!-- Panel with sealed pipeline -->
<section class="pipeline-panel pipeline-panel--sealed">
  <svg class="pipeline-art" viewBox="0 0 1200 557" xmlns="http://www.w3.org/2000/svg">
    <line x1="266" y1="163" x2="328" y2="163" stroke="#2dbb3a" stroke-width="2"/>
    <line x1="915" y1="163" x2="977" y2="163" stroke="#2dbb3a" stroke-width="2"/>
    <rect x="250" y="245" width="750" height="13" fill="#b6e2f6"/>
    <g fill="#2dbb3a">
      <rect x="298" y="243" width="4" height="17"/><rect x="327" y="243" width="4" height="17"/>
      <rect x="422" y="243" width="4" height="17"/><rect x="451" y="243" width="4" height="17"/>
      <rect x="546" y="243" width="4" height="17"/><rect x="575" y="243" width="4" height="17"/>
      <rect x="670" y="243" width="4" height="17"/><rect x="699" y="243" width="4" height="17"/>
      <rect x="794" y="243" width="4" height="17"/><rect x="823" y="243" width="4" height="17"/>
      <rect x="918" y="243" width="4" height="17"/><rect x="947" y="243" width="4" height="17"/>
    </g>
    <rect x="188" y="411" width="860" height="24" fill="#b6e2f6"/>
    <g fill="#1797d6">
      <rect x="186" y="406" width="5" height="34"/><rect x="193" y="406" width="3" height="34"/>
      <rect x="1043" y="406" width="3" height="34"/><rect x="1048" y="406" width="5" height="34"/>
      <rect x="306" y="408" width="4" height="30"/><rect x="312" y="408" width="4" height="30"/>
      <rect x="430" y="408" width="4" height="30"/><rect x="436" y="408" width="4" height="30"/>
      <rect x="554" y="408" width="4" height="30"/><rect x="560" y="408" width="4" height="30"/>
      <rect x="678" y="408" width="4" height="30"/><rect x="684" y="408" width="4" height="30"/>
      <rect x="802" y="408" width="4" height="30"/><rect x="808" y="408" width="4" height="30"/>
      <rect x="926" y="408" width="4" height="30"/><rect x="932" y="408" width="4" height="30"/>
    </g>
    <g fill="none" stroke="#a6ecc9" stroke-width="22">
      <path d="M253 367 V398 Q253 423 282 423"/>
      <path d="M377 367 V398 Q377 423 406 423"/>
      <path d="M501 367 V398 Q501 423 530 423"/>
      <path d="M625 367 V398 Q625 423 654 423"/>
      <path d="M749 367 V398 Q749 423 778 423"/>
      <path d="M873 367 V398 Q873 423 902 423"/>
      <path d="M997 367 V398 Q997 423 1026 423"/>
    </g>
    <g fill="#2dbb3a">
      <rect x="241" y="365" width="24" height="4"/><rect x="365" y="365" width="24" height="4"/>
      <rect x="489" y="365" width="24" height="4"/><rect x="613" y="365" width="24" height="4"/>
      <rect x="737" y="365" width="24" height="4"/><rect x="861" y="365" width="24" height="4"/>
      <rect x="985" y="365" width="24" height="4"/>
    </g>
    <g stroke="#1a9fdc" stroke-width="2" stroke-dasharray="2 3">
      <line x1="253" y1="437" x2="253" y2="490"/><line x1="376" y1="437" x2="376" y2="490"/>
      <line x1="500" y1="437" x2="500" y2="490"/><line x1="624" y1="437" x2="624" y2="490"/>
      <line x1="748" y1="437" x2="748" y2="490"/><line x1="872" y1="437" x2="872" y2="490"/>
      <line x1="996" y1="437" x2="996" y2="490"/>
    </g>
    <g fill="#111418">
      <rect x="233" y="493" width="40" height="48" rx="4" role="img" aria-label="Icon: sponsor with child"/>
      <rect x="362" y="493" width="28" height="48" rx="4" role="img" aria-label="Icon: young child"/>
      <rect x="480" y="493" width="40" height="48" rx="4" role="img" aria-label="Icon: student with science symbol"/>
      <rect x="604" y="493" width="40" height="48" rx="4" role="img" aria-label="Icon: person helping another up"/>
      <rect x="722" y="497" width="52" height="40" rx="4" role="img" aria-label="Icon: graduation cap"/>
      <rect x="850" y="493" width="44" height="48" rx="4" role="img" aria-label="Icon: two people shaking hands"/>
      <rect x="970" y="491" width="54" height="52" rx="4" role="img" aria-label="Icon: crowd of people"/>
    </g>
  </svg>

  <h2 class="panel-title">KESIMA Leadership Pipeline</h2>
  <p class="panel-subtitle">Developing a steady flow of servant leaders for Tanzania's future</p>

  <div class="stage-card" style="left:205px"><div class="stage-name">KESIMA Sponsorship Program</div><span class="stage-tag">OUTCOME</span><p class="stage-outcome">Establishing spiritual, academic,and health foundations</p></div>
  <div class="stage-card" style="left:329px"><div class="stage-name">KESIMA Primary School</div><span class="stage-tag">OUTCOME</span><p class="stage-outcome">Potential leaders with Biblical worldview and strong academic foundations.</p></div>
  <div class="stage-card" style="left:453px"><div class="stage-name">KESIMA Secondary School</div><span class="stage-tag">OUTCOME</span><p class="stage-outcome">Emerging leaders with concrete skills and strong servant mindset.</p></div>
  <div class="stage-card" style="left:577px"><div class="stage-name">KESIMA Service Leadership Experience</div><span class="stage-tag">OUTCOME</span><p class="stage-outcome">Growing servant leaders with practical experience to effect change for the kingdom</p></div>
  <div class="stage-card" style="left:701px"><div class="stage-name">KESIMA Higher Education Support</div><span class="stage-tag">OUTCOME</span><p class="stage-outcome">Expanding vision, capability, and motivation to solve bigger challenges for the nation.</p></div>
  <div class="stage-card" style="left:825px"><div class="stage-name">KESIMA Employment Center</div><span class="stage-tag">OUTCOME</span><p class="stage-outcome">Capable Christ-centered leaders in the marketplace as value adding employees and entrepreneurs.</p></div>
  <div class="stage-card" style="left:949px"><div class="stage-name">KESIMA Leadership Hub</div><span class="stage-tag">OUTCOME</span><p class="stage-outcome">Mature Christian leaders being placed and positioned for leadership roles in the community and nation.</p></div>
</section>

</body>
</html>
```